Webdesign für Heilpraktiker
Zielgruppe
Ich bin Heilpraktiker und betreibe eine Naturheilpraxis mit den Schwerpunkten der traditionellen chinesischen Medizin (TCM). Da ganz besonders in der Philosophie (sogenannte 'Schule' des Wo Shen). Aber auch in der traditionellen Heilweise der TCM, wie Akupunktur, Heilkräutermedizin und weiteres.
Die Zielgruppe sind Menschen, die medizinische Hilfe benötigen. (Vom Kind bis zum älteren Menschen).
Aufgabenstellung
Es gibt ein Praxislogo, ein Foto von mir und ggf. ein Landschaftsbild. Ich dachte an fünf Hauptseiten mit Untergruppen. Am Ende sollte alles in Wordpress formatiert werden können, um es zu veröffentlichen.
Weitere Fotos zur Unterstützung der Themen kann ich natürlich gerne liefern.
Die Gestaltung ist nicht festgesetzt. Sollte aber seriös rüber kommen.

```html
<!DOCTYPE html>
<html lang="de">
<head>
<meta charset="utf-8">
<title>Naturheilpraxis Jonas Feldkamp</title>
<link href="https://fonts.googleapis.com/css2?family=Lato:wght@400;700;900&display=swap" rel="stylesheet">
<style>
:root{
  --gold:#d8ac6a;
  --dark:#3c3c3c;
  --text:#333;
  --muted:#8a8a8a;
  --light:#f5f5f5;
  --line:#e3e3e3;
  --white:#fff;
}
*{box-sizing:border-box;margin:0;padding:0}
html,body{width:1200px;height:2931px;overflow:hidden}
body{font-family:'Lato',sans-serif;color:var(--text);background:var(--white);position:relative;font-size:13px;line-height:1.5}
.abs{position:absolute}
.img-fill{position:absolute}
.heading{position:absolute;color:var(--gold);font-weight:700;letter-spacing:2px;font-size:16px;text-transform:uppercase;white-space:nowrap}
.more{position:absolute;color:var(--gold);text-decoration:underline;font-size:12px}

.hero{left:0;top:0;width:1200px;height:519px;background:linear-gradient(180deg,#3f6b2a 0%,#6f9a3c 35%,#4d7a2c 70%,#2f4f1f 100%)}
.hero-title{left:0;top:341px;width:1200px;text-align:center;color:#fff;font-size:41px;line-height:48px;font-weight:400}
.hero-title b{font-weight:900}
.topbar{left:150px;top:0;width:900px;height:88px;background:var(--white)}
.brand{left:162px;top:24px;display:flex;align-items:center;gap:8px;font-weight:700;font-size:13px;color:var(--dark);width:140px;line-height:1.2}
.brand .dot{width:28px;height:28px;border-radius:50%;background:var(--gold);flex:none}
.contact-top{top:10px;display:flex;align-items:center;gap:8px;font-size:12px;color:var(--text);white-space:nowrap}
.ico{width:24px;height:24px;border-radius:50%;background:var(--gold);display:flex;align-items:center;justify-content:center}
.nav{left:313px;top:48px;width:737px;height:40px;background:var(--gold);display:flex;justify-content:space-between;padding-right:16px}
.nav a{font-size:11px;font-weight:700;color:var(--dark);text-decoration:none;display:flex;align-items:center;text-transform:uppercase;white-space:nowrap;letter-spacing:-.1px}
.nav a.active{background:var(--dark);color:#fff;padding:0 19px}

.about{left:0;top:519px;width:1200px;height:329px;background:var(--light);border-bottom:1px solid var(--line)}
.about-name{left:188px;top:568px;font-size:22px;letter-spacing:3px;color:var(--gold);font-weight:700;white-space:nowrap}
.about-sub{left:188px;top:601px;font-size:13px;line-height:15px;width:480px}
.checklist{left:188px;top:648px;list-style:none}
.checklist li{height:30px;display:flex;align-items:center;gap:16px;font-size:13px;white-space:nowrap}
.portrait{left:749px;top:560px;width:314px;height:314px;border-radius:50%;background:var(--gold);padding:14px}
.portrait div{width:100%;height:100%;border-radius:50%;background:linear-gradient(160deg,#8a9fb5,#3a4a5e)}

.card-text{position:absolute;font-size:12.5px;line-height:20px;white-space:nowrap}

.help{left:0;top:1325px;width:1200px;height:452px;border:1px solid var(--line)}
.help-split{left:600px;top:1325px;width:1px;height:452px;background:var(--line)}
.help-intro{left:150px;top:1393px;font-weight:700;font-size:12.5px;line-height:20px;white-space:nowrap}
.help-list{left:150px;top:1453px;list-style:none}
.help-list li{display:flex;gap:14px;font-size:12.5px;line-height:19px;margin-bottom:11px;white-space:nowrap}
.btn{left:151px;top:1697px;width:128px;height:39px;background:var(--gold);color:var(--dark);font-size:13px;display:flex;align-items:center;justify-content:center;gap:8px}

.testi-bg{left:0;top:2290px;width:1200px;height:495px;background:#f2f2f2}
.quote{font-size:150px;font-weight:900;color:var(--gold);line-height:1}
.testi-title{left:280px;top:2363px;font-size:16px;font-weight:700;letter-spacing:1.5px;color:var(--dark);white-space:nowrap}
.testi-box{left:150px;top:2410px;width:477px;height:168px;background:#fff;border:1px solid var(--line);border-radius:4px;padding:26px 28px;font-size:12.5px;line-height:22.5px}
.avatar{left:156px;top:2591px;width:46px;height:46px;border-radius:50%;background:linear-gradient(#cfc8c0,#8d8177);border:3px solid #fff}
.dots{left:354px;top:2652px;display:flex;gap:6px}
.dots span{width:8px;height:8px;border-radius:50%;background:var(--dark)}
.dots span:first-child{background:var(--gold)}
.form{left:669px;top:2347px;width:360px;height:373px;background:var(--gold);padding:20px 15px}
.form h3{text-align:center;font-size:16px;letter-spacing:1.5px;color:var(--dark);font-weight:700;margin-bottom:14px}
.field{background:#fff;border:1px solid #e6d5b8;height:35px;margin-bottom:7px;font-size:11px;color:var(--muted);padding:10px 16px}
.field.area{height:118px}
.send{background:var(--dark);color:#fff;height:43px;display:flex;align-items:center;justify-content:center;gap:12px;font-size:14px;letter-spacing:1px;margin-top:8px}

.footer{left:0;top:2785px;width:1200px;height:146px;background:#3d3d3d;color:#a8a8a8;font-size:12px;line-height:18px}
.foot-col{position:absolute;display:flex;gap:10px;white-space:nowrap}
</style>
</head>
<body>

<div class="abs hero" role="img" aria-label="Hände halten eine junge Pflanze in Erde vor grünem Wald"></div>
<h1 class="abs hero-title"><b>Naturheilpraxis</b> des<br>Heilpraktiker Jonas Feldkamp</h1>

<div class="abs topbar"></div>
<div class="abs brand"><span class="dot"></span>Naturheilpraxis Feldkamp</div>
<div class="abs contact-top" style="left:679px">
  <span class="ico"><svg width="12" height="12" viewBox="0 0 24 24" fill="none" stroke="#fff" stroke-width="2"><path d="M5 3h4l2 5-3 2a11 11 0 0 0 6 6l2-3 5 2v4a2 2 0 0 1-2 2A17 17 0 0 1 3 5a2 2 0 0 1 2-2z"/></svg></span>04712 – 480 27 16</div>
<div class="abs contact-top" style="left:822px">
  <span class="ico"><svg width="12" height="12" viewBox="0 0 24 24" fill="none" stroke="#fff" stroke-width="2"><rect x="3" y="5" width="18" height="14"/><path d="M3 5l9 8 9-8"/></svg></span>post@heilpraktiker-feldkamp.de</div>
<nav class="abs nav">
  <a class="active">Startseite</a><a>Zu meiner Person</a><a>Wobei kann ich helfen</a><a>Der erste Besuch</a><a>Was ist das Wo Shen</a><a>Kontakt</a>
</nav>

<section class="abs about"></section>
<h2 class="abs about-name">JONAS FELDKAMP</h2>
<p class="abs about-sub">Heilpraktiker und zertifizierter Therapeut der traditionellen chinesischen Medizin<br>(Berufsverband BVN e.V.)</p>
<ul class="abs checklist">
  <li><svg width="22" height="22" viewBox="0 0 22 22" fill="none"><circle cx="11" cy="11" r="9" stroke="#333" stroke-width="1.5"/><path d="M6 11l4 4 9-10" stroke="#d8ac6a" stroke-width="2"/></svg>Jahrgang 1971</li>
  <li><svg width="22" height="22" viewBox="0 0 22 22" fill="none"><circle cx="11" cy="11" r="9" stroke="#333" stroke-width="1.5"/><path d="M6 11l4 4 9-10" stroke="#d8ac6a" stroke-width="2"/></svg>Seit 2008 Heilpraktiker in Hohenmoor</li>
  <li><svg width="22" height="22" viewBox="0 0 22 22" fill="none"><circle cx="11" cy="11" r="9" stroke="#333" stroke-width="1.5"/><path d="M6 11l4 4 9-10" stroke="#d8ac6a" stroke-width="2"/></svg>Seit 2012 Gründer und Leiter des NWB Blutanalyselabors in Hohenmoor</li>
  <li><svg width="22" height="22" viewBox="0 0 22 22" fill="none"><circle cx="11" cy="11" r="9" stroke="#333" stroke-width="1.5"/><path d="M6 11l4 4 9-10" stroke="#d8ac6a" stroke-width="2"/></svg>Seit 2017 zertifizierter TCM Therapeut (Berufsverband BVN e.V.)</li>
  <li><svg width="22" height="22" viewBox="0 0 22 22" fill="none"><circle cx="11" cy="11" r="9" stroke="#333" stroke-width="1.5"/><path d="M6 11l4 4 9-10" stroke="#d8ac6a" stroke-width="2"/></svg>Beschäftigung mit der Wo Shen Philosophie (Schule) seit 1993</li>
</ul>
<div class="abs portrait"><div role="img" aria-label="Porträtfoto des Heilpraktikers"></div></div>

<h2 class="heading" style="left:149px;top:940px">Was mache ich</h2>
<div class="img-fill" style="left:149px;top:975px;width:428px;height:230px;background:linear-gradient(135deg,#dfeaf3,#9dbad2)" role="img" aria-label="Medizinische Symbole über behandschuhter Hand"></div>
<p class="card-text" style="left:149px;top:1216px">Seit vielen Jahrzehnten begeistere ich mich für die Themen der Medizin<br>und die Wiederherstellung der Gesundheit.</p>
<span class="more" style="left:151px;top:1273px">Mehr...</span>

<h2 class="heading" style="left:622px;top:940px">Die Praxis</h2>
<div class="img-fill" style="left:622px;top:975px;width:427px;height:230px;background:linear-gradient(135deg,#f2f2f2,#9a9a9a)" role="img" aria-label="Mikroskop und Blutprobe im Labor"></div>
<p class="card-text" style="left:622px;top:1216px;line-height:22px">Seit 2014 besteht die Praxis, in der sich auch das NWB Blutanalyselabor<br>befindet, im dritten Stock eines Wohn- und Geschäftshauses in der...</p>
<span class="more" style="left:623px;top:1274px">Mehr...</span>

<section class="abs help"></section>
<div class="abs help-split"></div>
<h2 class="heading" style="left:150px;top:1362px">Wobei kann ich helfen</h2>
<p class="abs help-intro">Der Schwerpunkt meiner Tätigkeit ist die Beseitigung und Linderung<br>von chronischen Erkrankungen und deren Folgen. Hierzu zählen u.a.:</p>
<ul class="abs help-list">
  <li><svg width="16" height="16" viewBox="0 0 16 16" style="flex:none;margin-top:2px"><path d="M2 8l4 4 8-9" fill="none" stroke="#d8ac6a" stroke-width="1.8"/></svg><span>Der rheumatische Formenkreis / Erkrankungen die mit Entzünd-<br>ungen und Schmerzzuständen einhergehen</span></li>
  <li><svg width="16" height="16" viewBox="0 0 16 16" style="flex:none;margin-top:2px"><path d="M2 8l4 4 8-9" fill="none" stroke="#d8ac6a" stroke-width="1.8"/></svg><span>Magen- und Darmbeschwerden / Unverträglichkeiten bis hin zu<br>allergischen Dispositionen</span></li>
  <li><svg width="16" height="16" viewBox="0 0 16 16" style="flex:none;margin-top:2px"><path d="M2 8l4 4 8-9" fill="none" stroke="#d8ac6a" stroke-width="1.8"/></svg>Diabetes / Stoffwechselstörungen</li>
  <li><svg width="16" height="16" viewBox="0 0 16 16" style="flex:none;margin-top:2px"><path d="M2 8l4 4 8-9" fill="none" stroke="#d8ac6a" stroke-width="1.8"/></svg>Chronische virale- und bakterielle Belastungen</li>
  <li><svg width="16" height="16" viewBox="0 0 16 16" style="flex:none;margin-top:2px"><path d="M2 8l4 4 8-9" fill="none" stroke="#d8ac6a" stroke-width="1.8"/></svg>Belastungen psychischer Natur / Erschöpfungszustände</li>
  <li><svg width="16" height="16" viewBox="0 0 16 16" style="flex:none;margin-top:2px"><path d="M2 8l4 4 8-9" fill="none" stroke="#d8ac6a" stroke-width="1.8"/></svg>Long Covid Belastungen</li>
</ul>
<div class="abs btn"><svg width="12" height="10" viewBox="0 0 12 10"><path d="M0 5h10M7 1l4 4-4 4" fill="none" stroke="#3c3c3c" stroke-width="1.3"/></svg>Lern mehr</div>
<div class="img-fill" style="left:630px;top:1350px;width:545px;height:400px;background:radial-gradient(circle at 50% 50%,#fbeeee,#ffffff 70%)" role="img" aria-label="Illustration medizinischer Symbole im Halbkreis"></div>

<h2 class="heading" style="left:149px;top:1833px">Der erste Besuch</h2>
<div class="img-fill" style="left:149px;top:1868px;width:428px;height:230px;background:linear-gradient(135deg,#6b6b6b,#e8ecf0)" role="img" aria-label="Arzt notiert Anamnese auf Klemmbrett"></div>
<p class="card-text" style="left:149px;top:2109px">Am Anfang steht eine einstündige Anamnese mit ausführlicher Interpre-<br>tation ihrer bisherigen Untersuchungsergebnisse und Laborberichten.<br>Gegebenfalls werden weitere Laboraufträge zur Diagnosesicherung und<br>Verlaufskontrolle beauftragt.</p>
<span class="more" style="left:151px;top:2206px">Mehr...</span>

<h2 class="heading" style="left:622px;top:1833px">Was ist das Wo Shen</h2>
<div class="img-fill" style="left:622px;top:1868px;width:427px;height:230px;background:linear-gradient(180deg,#8fb3c9,#d9c7ad 55%,#6d8a96)" role="img" aria-label="Läufer am Seeufer in der Abenddämmerung"></div>
<p class="card-text" style="left:622px;top:2109px;line-height:22px">Das Wo Shen ist aus unserer heutigen Sicht ein Ratgeber für ein harmonis-<br>ches und gesundes Sein, im Zusammenleben mit allen Lebensformen.</p>
<span class="more" style="left:623px;top:2166px">Mehr...</span>

<section class="abs testi-bg"></section>
<div class="abs quote" style="left:146px;top:2312px">“</div>
<div class="abs testi-title">WAS UNSER KUNDE SAGT</div>
<div class="abs testi-box">Lorem ipsum dolor sit amet, consectetur adipiscing elit, sed do eiusmod tempor incididunt ut labore et dolore magna aliqua. Ut enim ad minim veniam, quis nostrud exercitation ullamco laboris nisi ut aliquip ex ea commodo consequat. Duis aute irure dolor in reprehenderit in voluptate velit esse cillum dolore eu fugiat nulla pariatur.</div>
<div class="abs quote" style="left:530px;top:2550px">”</div>
<div class="abs avatar" role="img" aria-label="Kundenfoto"></div>
<div class="abs" style="left:214px;top:2605px;font-weight:700;font-size:13px;color:var(--dark)">Milan Kessel</div>
<div class="abs dots"><span></span><span></span><span></span><span></span><span></span></div>

<form class="abs form">
  <h3>SCHNELLER KONTAKT</h3>
  <div class="field">Vollständiger Name</div>
  <div class="field">Email</div>
  <div class="field">Telefon</div>
  <div class="field area">Ihre Anfrage</div>
  <div class="send"><svg width="16" height="16" viewBox="0 0 24 24" fill="none" stroke="#fff" stroke-width="1.5"><path d="M22 2L2 11l8 3 3 8z M10 14L22 2"/></svg>SENDEN</div>
</form>

<footer class="abs footer">
  <div class="foot-col" style="left:155px;top:42px;align-items:center;color:#d0d0d0;font-weight:700"><span style="width:30px;height:30px;border-radius:50%;background:var(--gold)"></span>Praxis Feldkamp</div>
  <div class="foot-col" style="left:342px;top:32px"><svg width="14" height="18" viewBox="0 0 14 18"><path d="M7 1a6 6 0 0 1 6 6c0 4-6 10-6 10S1 11 1 7a6 6 0 0 1 6-6z" fill="#d8ac6a"/><circle cx="7" cy="7" r="2" fill="#3d3d3d"/></svg><div>Jonas Feldkamp<br>Lindenweg 14<br>27419 Hohenmoor</div></div>
  <div class="foot-col" style="left:600px;top:32px"><svg width="14" height="14" viewBox="0 0 24 24" fill="none" stroke="#d8ac6a" stroke-width="2"><path d="M5 3h4l2 5-3 2a11 11 0 0 0 6 6l2-3 5 2v4a2 2 0 0 1-2 2A17 17 0 0 1 3 5a2 2 0 0 1 2-2z"/></svg>Telefon 04712 – 480 27 16</div>
  <div class="foot-col" style="left:600px;top:58px"><svg width="14" height="14" viewBox="0 0 24 24" fill="none" stroke="#d8ac6a" stroke-width="2"><rect x="3" y="5" width="18" height="14"/><path d="M3 5l9 8 9-8"/></svg>post@heilpraktiker-feldkamp.de</div>
  <div class="foot-col" style="left:931px;top:34px">Impressum</div>
  <div class="foot-col" style="left:931px;top:56px">Datenschutzerkiärung</div>
</footer>

</body>
</html>
```